Visitenkarten/Briefpaier/Kassenkassenbelege für Juwelier
Zielgruppe
Mittelständischer Juwelier mit zwei Filialen. Klassischer Schmuck, Uhren und Modeschmuck
Aufgabenstellung
Es müssen für zwei Geschäfte Visitenkarten, Briefpapier (A4) und Kassenkassenbelege (A6) erstellt werden. Logo und Typo im Anhang. Ein Farbkonzept besteht noch nicht. Die Idee geht in Richtung Bordeaux-Rot.
Generell:
(1) Sieht erstmal nach viel Beschreibung aus, bitte nicht entmutigen lassen, sind zu 90% nur austauschbare Inhalts-/Kontaktdaten.
(2) Für meine Zwecke reicht es vollkommen aus, wenn bei den Vorschlägen zur Arbeitsersparnis erstmal nur mit einer Adresse gearbeitet wird. Wenn ich dann den zutreffenden Designvorschlag gefunden habe, können wir die zweite Adresse in dem ersten Format umsetzen. Ich denke das spart Zeit und Nerven.
(3) Bitte Angaben wie "Tel.:" oder "USt.- ID:" nicht wörtlich nehmen, es soll dabei klar sein worum es geht; wenn "Telefon" ausgeschrieben besser aussieht, bitte in der optisch ansprechenderen Form verwenden.
(4) Bei Fragen, bitte fragen!
(5) Viel Spass bei dem Projekt - Ich freu' mich auf die Vorschläge!
Visitenkarten(1):
Juwelier Brenneck GmbH
www.juwelier-brenneck-beispiel.de
Visitenkarten(2):
Visitenkarten(generell):
(1) Die einzelnen Daten können durch Hervorhebungen wie Adresse, Kontakt, Online/Internet unterteilt bzw. hervorgehoben werden.
(2) Die Visitenkarten sollen farbig gedruckt werden; geplant ist weiß als Hintergrund ist aber nicht zwingend bei einer guten anderen Idee
Briefpapier:
(1)Absender im Adressfeld für DIN-lang Briefumschläge mit Fenster:
(2)Informationen im Footer/Seitenbereich:
Juwelier Brenneck Gmb..

```html
<!DOCTYPE html>
<html lang="de">
<head>
<meta charset="utf-8">
<title>Juwelier Brenneck – Visitenkarte</title>
<link href="https://fonts.googleapis.com/css2?family=Source+Sans+3:wght@400;600&display=swap" rel="stylesheet">
<style>
  :root {
    --bordeaux: #7d1c35;
    --stone: #9a9a9a;
    --stone-light: #d4d4d4;
    --paper: #f6f6f6;
    --backdrop: #e4e4e4;
    --white: #ffffff;
  }
  * { margin: 0; padding: 0; box-sizing: border-box; }
  html, body { width: 1200px; height: 800px; overflow: hidden; }
  body {
    background: var(--backdrop);
    font-family: "Source Sans 3", "Source Sans Pro", sans-serif;
    display: flex;
    align-items: center;
    justify-content: center;
    gap: 60px;
  }
  .card {
    position: relative;
    width: 510px;
    height: 330px;
    overflow: hidden;
    box-shadow: 0 6px 24px rgba(0,0,0,0.12);
  }

  /* Front */
  .card--front { background: var(--bordeaux); color: var(--white); }
  .front__mark {
    position: absolute;
    left: 70px; top: 72px;
    width: 78px; height: 78px;
    background: var(--white);
  }
  .front__name {
    position: absolute;
    left: 70px; top: 176px;
    font-size: 40px;
    font-weight: 600;
    letter-spacing: 1px;
    text-transform: uppercase;
    color: var(--stone-light);
  }
  .front__rule {
    position: absolute;
    left: 70px; top: 240px;
    width: 360px; height: 1px;
    background: var(--stone-light);
  }
  .front__tab {
    position: absolute;
    right: 0; top: 210px;
    width: 48px; height: 44px;
    background: var(--stone);
  }

  /* Back */
  .card--back { background: var(--paper); }
  .back__mark {
    position: absolute;
    left: 60px; top: 60px;
    width: 56px; height: 56px;
    background: var(--stone);
  }
  .back__info {
    position: absolute;
    left: 60px; top: 160px;
    font-size: 17px;
    line-height: 1.45;
  }
  .back__company {
    color: var(--stone);
    font-weight: 600;
    text-transform: uppercase;
    letter-spacing: 0.5px;
  }
  .back__address { color: var(--bordeaux); }
  .back__contact { color: var(--bordeaux); }
  .back__label { color: var(--stone); margin-right: 4px; }
  .back__web { color: var(--bordeaux); }
  .back__tab {
    position: absolute;
    right: 0; top: 220px;
    width: 48px; height: 44px;
    background: var(--bordeaux);
  }
</style>
</head>
<body>
  <section class="card card--front" aria-label="Vorderseite">
    <div class="front__mark"></div>
    <div class="front__name">Juwelier Brenneck</div>
    <div class="front__rule"></div>
    <div class="front__tab"></div>
  </section>

  <section class="card card--back" aria-label="Rückseite">
    <div class="back__mark"></div>
    <div class="back__info">
      <p class="back__company">Juwelier Brenneck GmbH</p>
      <p class="back__address">Lindenallee 12 in 45100 Musterstadt</p>
      <p class="back__contact">
        <span class="back__label">TEL</span>0201-555010&nbsp;&nbsp;
        <span class="back__label">FAX</span>0201-555011
      </p>
      <p class="back__contact">info@juwelier-brenneck-beispiel.de</p>
      <p class="back__web">www.juwelier-brenneck-beispiel.de</p>
    </div>
    <div class="back__tab"></div>
  </section>
</body>
</html>
```